Innovative cost reduction consultant needs to build a group of technical advisors

We need to share our message and compassion for developing cost reduction in the automotive industry. We create opportunities for immediate innovation, by developing cost reduction solutions across suppliers with related process. Attached is an existing Power Point, but it needs improvement. Most of all, a good compelling story, why experts should join us.

Target Market(s)

Automotive industry, supply chain management

Industry/Entity Type

Automotive

Font styles to use
Serif
Sans Serif

Requirements
Must have
• Better visual graphics. There are a few, but they are not as visually appearing as I would like. A graphic with data should have a better visual impact then the ones that I created. I would like to share the message, that I am providing a solution for the automotive industry. The goal is to reduce costs and improve supplier and OEM relationships. The objective is to do so by creating opportunities for immediate innovation, by developing cost reduction solutions across suppliers with related processes. This message may need a visual graphic, which is missing from the presentation.
Nice to have
• Challenge my story and presentation. Does this make sense to you, and what is your opinions of the subject. Or, a relevant news source to validate the story.
Should not have
• I have not decided on the name of the venture or logo. So, let's just use my name as the source or writer. Marcus Delby, Cost Reduction Specialist. Thanks,

```html
<!DOCTYPE html>
<html lang="en">
<head>
<meta charset="utf-8">
<title>Supplier Dashboard</title>
<link rel="stylesheet" href="https://fonts.googleapis.com/css2?family=Roboto+Condensed:wght@300;400;700&family=Roboto:wght@400;700&display=swap">
<style>
  :root {
    --band-blue: #0a4ea2;
    --foot-blue: #1a9be2;
    --ink: #555a5f;
    --ink-dark: #333;
    --panel: #ffffff;
    --red: #cc4740;
    --red-dark: #a8302a;
    --red-light: #e3837c;
    --rose: #e9a19b;
    --crimson: #8c1f1f;
    --teal: #2a7f78;
    --teal-dark: #1f5c55;
    --teal-soft: #a3d8d0;
    --bar-teal: #1f7f86;
    --bubble: #4f6c66;
    --rule: #9a9a9a;
  }
  * { margin: 0; padding: 0; box-sizing: border-box; }
  html, body { width: 1200px; height: 650px; overflow: hidden; background: #fff; }
  .slide { position: relative; width: 1200px; height: 650px; overflow: hidden; background: #fff; font-family: "Roboto Condensed", Arial, sans-serif; }
  .title-band { position: absolute; left: 0; top: 0; width: 1200px; height: 99px; background: var(--band-blue); }
  .slide-title { position: absolute; left: 79px; top: 47px; font-size: 42px; font-weight: 700; color: #fff; letter-spacing: -0.3px; line-height: 1; }
  .shade { position: absolute; left: 764px; top: 99px; width: 436px; height: 500px; background: linear-gradient(90deg, #ffffff 0%, #e9e9e9 55%, #c9c9c9 100%); }
  .points { position: absolute; left: 79px; top: 116px; list-style: none; width: 300px; }
  .points li { position: relative; padding-left: 32px; font-size: 22px; font-weight: 300; color: var(--ink); line-height: 27px; margin-bottom: 7.5px; }
  .points li::before { content: ""; position: absolute; left: 0; top: 5px; border-left: 8px solid var(--band-blue); border-top: 7px solid transparent; border-bottom: 7px solid transparent; }
  .dashboard { position: absolute; left: 363px; top: 124px; width: 761px; height: 471px; background: var(--panel); }
  .dashboard svg { display: block; width: 100%; height: 100%; }
  .dashboard text { font-family: "Roboto", Arial, sans-serif; fill: var(--ink-dark); }
  .dashboard .donut-labels text { fill: #fff; }
  .foot-band { position: absolute; left: 0; top: 622px; width: 1200px; height: 28px; background: var(--foot-blue); }
</style>
</head>
<body>
<div class="slide">
  <div class="title-band"></div>
  <h1 class="slide-title">Supplier Dashboard</h1>
  <div class="shade"></div>
  <ul class="points">
    <li>Web access to best practices</li>
    <li>Calculation tools</li>
    <li>Shared best efforts</li>
    <li>Means to implement best practices</li>
  </ul>

  <div class="dashboard">
    <svg viewBox="285 97 597 370" preserveAspectRatio="none" aria-label="Supplier performance dashboard">
      <!-- section rules -->
      <g class="rules" stroke="var(--rule)" stroke-width="0.8">
        <line x1="287" y1="305" x2="551" y2="305"/>
        <line x1="558" y1="125" x2="558" y2="455"/>
        <line x1="723" y1="125" x2="723" y2="327"/>
        <line x1="565" y1="332" x2="876" y2="332"/>
      </g>

      <!-- donut chart -->
      <g class="donut-legend">
        <text x="300" y="150" font-size="9" font-weight="700">Sample text</text>
        <text x="300" y="163" font-size="6.5">This is a sample text.</text>
        <text x="300" y="171" font-size="6.5">Insert your desired text here.</text>
        <rect x="290" y="195" width="7" height="4" fill="var(--red-dark)"/>
        <text x="300" y="199" font-size="5.5">This is a sample text</text><text x="300" y="206" font-size="5.5">Insert your desired text here.</text>
        <rect x="290" y="218" width="7" height="4" fill="var(--rose)"/>
        <text x="300" y="222" font-size="5.5">This is a sample text.</text><text x="300" y="229" font-size="5.5">Insert your desired text here.</text>
        <rect x="290" y="241" width="7" height="4" fill="var(--red)"/>
        <text x="300" y="245" font-size="5.5">This is a sample text</text><text x="300" y="252" font-size="5.5">Insert your desired text here.</text>
        <rect x="290" y="264" width="7" height="4" fill="var(--teal)"/>
        <text x="300" y="268" font-size="5.5">This is a sample text</text><text x="300" y="275" font-size="5.5">Insert your desired text here.</text>
      </g>
      <g class="donut" transform="rotate(-90 457 217)" fill="none">
        <circle cx="457" cy="217" r="73" stroke="var(--red)" stroke-width="18" pathLength="100" stroke-dasharray="56 100"/>
        <circle cx="457" cy="217" r="73" stroke="var(--teal)" stroke-width="18" pathLength="100" stroke-dasharray="26 100" stroke-dashoffset="-56"/>
        <circle cx="457" cy="217" r="73" stroke="var(--red-dark)" stroke-width="18" pathLength="100" stroke-dasharray="10 100" stroke-dashoffset="-82"/>
        <circle cx="457" cy="217" r="73" stroke="var(--red-light)" stroke-width="18" pathLength="100" stroke-dasharray="8 100" stroke-dashoffset="-92"/>
        <circle cx="457" cy="217" r="54" stroke="var(--rose)" stroke-width="11"/>
        <circle cx="457" cy="217" r="54" stroke="var(--teal)" stroke-width="11" pathLength="100" stroke-dasharray="37 100" stroke-dashoffset="-25"/>
        <circle cx="457" cy="217" r="46" stroke="#fff" stroke-width="3"/>
        <circle cx="457" cy="217" r="30" stroke="var(--red)" stroke-width="28" pathLength="100" stroke-dasharray="8 100"/>
        <circle cx="457" cy="217" r="30" stroke="var(--teal)" stroke-width="28" pathLength="100" stroke-dasharray="21 100" stroke-dashoffset="-8"/>
        <circle cx="457" cy="217" r="30" stroke="var(--red-dark)" stroke-width="28" pathLength="100" stroke-dasharray="30 100" stroke-dashoffset="-29"/>
        <circle cx="457" cy="217" r="30" stroke="var(--red)" stroke-width="28" pathLength="100" stroke-dasharray="8 100" stroke-dashoffset="-59"/>
        <circle cx="457" cy="217" r="30" stroke="var(--red-light)" stroke-width="28" pathLength="100" stroke-dasharray="33 100" stroke-dashoffset="-67"/>
      </g>
      <circle cx="457" cy="217" r="14" fill="#fff" stroke="#c8c8c8" stroke-width="1.5"/>
      <g class="donut-labels" font-size="5.5" font-weight="700" text-anchor="middle">
        <!-- outer ring -->
        <text x="439" y="148">9%</text>
        <text x="404" y="169">10%</text>
        <text x="528" y="234">58%</text>
        <text x="390" y="246">27%</text>
        <!-- middle ring -->
        <text x="495" y="181">39%</text>
        <text x="419" y="181">31%</text>
        <text x="484" y="266">57%</text>
        <text x="413" y="250">13%</text>
        <!-- inner pie -->
        <text x="464" y="190">8%</text>
        <text x="485" y="207">21%</text>
        <text x="431" y="204">33%</text>
        <text x="468" y="247">30%</text>
      </g>

      <!-- bubble chart -->
      <g class="bubbles">
        <text x="572" y="135" font-size="6.5">This is a sample text</text>
        <text x="572" y="143" font-size="6.5">Insert your desired text here.</text>
        <g fill="var(--bubble)" stroke="#fff" stroke-width="1">
          <circle cx="627" cy="187" r="33"/>
          <circle cx="659" cy="213" r="17"/>
          <circle cx="631" cy="240" r="22"/>
          <circle cx="622" cy="277" r="15"/>
          <circle cx="645" cy="283" r="9"/>
          <circle cx="624" cy="298" r="10"/>
          <circle cx="636" cy="310" r="9"/>
        </g>
        <g text-anchor="middle">
          <text x="627" y="192" font-size="13" style="fill:#fff">55%</text>
          <text x="662" y="216" font-size="8" style="fill:#fff">27%</text>
          <text x="638" y="244" font-size="10" style="fill:#fff">45%</text>
          <text x="622" y="280" font-size="7.5" style="fill:#fff">30%</text>
        </g>
        <g stroke="#555" stroke-width="0.6" fill="none">
          <line x1="670" y1="283" x2="655" y2="283"/>
          <line x1="591" y1="298" x2="613" y2="298"/>
          <line x1="670" y1="310" x2="646" y2="310"/>
        </g>
        <g fill="#555">
          <path d="M654 283 l3 -1.5 v3z"/><path d="M614 298 l-3 -1.5 v3z"/><path d="M645 310 l3 -1.5 v3z"/>
        </g>
        <text x="681" y="286" font-size="6">12%</text>
        <text x="578" y="300" font-size="6">15%</text>
        <text x="675" y="312" font-size="6">10%</text>
      </g>

      <!-- ring gauges -->
      <g class="gauges">
        <text x="734" y="135" font-size="6.5">This is a sample text.</text>
        <text x="734" y="143" font-size="6.5">Insert your desired</text>
        <text x="734" y="151" font-size="6.5">text here.</text>
        <g fill="none">
          <g transform="translate(828 138)">
            <circle r="11" stroke="var(--teal-soft)" stroke-width="2.5"/>
            <circle r="12" stroke="var(--teal-dark)" stroke-width="6" pathLength="100" stroke-dasharray="40 100" transform="rotate(-90)"/>
          </g>
          <g transform="translate(770 187)">
            <circle r="11" stroke="var(--teal-soft)" stroke-width="2.5"/>
            <circle r="12" stroke="var(--teal-dark)" stroke-width="6" pathLength="100" stroke-dasharray="52 100" transform="rotate(-90)"/>
          </g>
          <g transform="translate(828 187)">
            <circle r="11" stroke="var(--teal-soft)" stroke-width="2.5"/>
            <circle r="12" stroke="var(--teal-dark)" stroke-width="6" pathLength="100" stroke-dasharray="36 100" transform="rotate(-90)"/>
          </g>
          <g transform="translate(770 241)">
            <circle r="11" stroke="var(--teal-soft)" stroke-width="2.5"/>
            <circle r="12" stroke="var(--teal-dark)" stroke-width="6" pathLength="100" stroke-dasharray="20 100" transform="rotate(-90)"/>
          </g>
          <g transform="translate(828 241)">
            <circle r="11" stroke="var(--teal-soft)" stroke-width="2.5"/>
            <circle r="12" stroke="var(--teal-dark)" stroke-width="6" pathLength="100" stroke-dasharray="52 100" transform="rotate(-90)"/>
          </g>
          <g transform="translate(770 295)">
            <circle r="11" stroke="var(--teal-soft)" stroke-width="2.5"/>
            <circle r="12" stroke="var(--teal-dark)" stroke-width="6" pathLength="100" stroke-dasharray="20 100" transform="rotate(180)"/>
          </g>
          <g transform="translate(828 295)">
            <circle r="11" stroke="var(--teal-soft)" stroke-width="2.5"/>
            <circle r="12" stroke="var(--teal-dark)" stroke-width="6" pathLength="100" stroke-dasharray="17 100" transform="rotate(-150)"/>
          </g>
        </g>
        <g font-size="5.5" text-anchor="middle">
          <text x="828" y="140">40%</text><text x="828" y="159">Sample text</text>
          <text x="770" y="189">52%</text><text x="770" y="211">Sample text</text>
          <text x="828" y="189">36%</text><text x="828" y="211">Sample text</text>
          <text x="770" y="243">20%</text><text x="770" y="265">Sample text</text>
          <text x="828" y="243">52%</text><text x="828" y="265">Sample text</text>
          <text x="770" y="297">20%</text><text x="770" y="319">Sample text</text>
          <text x="828" y="297">17%</text><text x="828" y="319">Sample text</text>
        </g>
      </g>

      <!-- bar list -->
      <g class="bar-list">
        <text x="300" y="324" font-size="9">Sample text</text>
        <text x="300" y="336" font-size="6.5">This is a sample text.</text>
        <text x="300" y="344" font-size="6.5">Insert your desired text here.</text>
        <g fill="var(--bar-teal)">
          <path d="M298 350 H428 L421 359 H298Z"/>
          <path d="M298 369 H410 L403 378 H298Z"/>
          <path d="M298 388 H383 L376 397 H298Z"/>
          <path d="M298 406 H368 L361 415 H298Z"/>
          <path d="M298 425 H352 L345 434 H298Z"/>
          <path d="M298 444 H333 L326 453 H298Z"/>
        </g>
        <g font-size="5.5">
          <text x="302" y="356.5" style="fill:#fff">3.3</text><text x="411" y="356.5" style="fill:#fff">7</text>
          <text x="302" y="375.5" style="fill:#fff">3.3</text><text x="393" y="375.5" style="fill:#fff">8</text>
          <text x="302" y="394.5" style="fill:#fff">3.3</text><text x="366" y="394.5" style="fill:#fff">6</text>
          <text x="302" y="412.5" style="fill:#fff">3.3</text><text x="351" y="412.5" style="fill:#fff">4</text>
          <text x="302" y="431.5" style="fill:#fff">3.3</text><text x="335" y="431.5" style="fill:#fff">3</text>
          <text x="302" y="450.5" style="fill:#fff">3.3</text><text x="318" y="450.5" style="fill:#fff">2</text>
        </g>
        <g font-size="6.5">
          <text x="460" y="357">Insert your desired text here.</text>
          <text x="460" y="376">Insert your desired text here.</text>
          <text x="460" y="395">Insert your desired text here.</text>
          <text x="460" y="413">Insert your desired text here.</text>
          <text x="460" y="432">Insert your desired text here.</text>
          <text x="460" y="451">Insert your desired text here.</text>
        </g>
        <g stroke="#bbb" stroke-width="0.5">
          <line x1="298" y1="362" x2="553" y2="362"/>
          <line x1="298" y1="381" x2="553" y2="381"/>
          <line x1="298" y1="400" x2="553" y2="400"/>
          <line x1="298" y1="418" x2="553" y2="418"/>
          <line x1="298" y1="437" x2="553" y2="437"/>
        </g>
      </g>

      <!-- flow diagram -->
      <g class="flow">
        <text x="598" y="348" font-size="9">Sample text</text>
        <text x="598" y="358" font-size="6.5">This is a sample text</text>
        <text x="598" y="366" font-size="6.5">Insert your desired text here.</text>
        <g stroke="#777" stroke-width="0.7" fill="none">
          <path d="M735 366 H708 V383 H677"/>
          <path d="M771 366 H798 V383 H829"/>
          <path d="M735 372 H712 V432 H694"/>
          <path d="M771 372 H794 V432 H813"/>
          <path d="M753 386 V408"/>
        </g>
        <g fill="#777">
          <path d="M676 383 l4 -2 v4z"/><path d="M830 383 l-4 -2 v4z"/>
          <path d="M693 432 l4 -2 v4z"/><path d="M814 432 l-4 -2 v4z"/>
          <path d="M753 385 l-2 4 h4z"/><path d="M753 409 l-2 -4 h4z"/>
          <path d="M736 366 l-4 -2 v4z"/><path d="M770 366 l4 -2 v4z"/>
        </g>
        <g fill="var(--crimson)">
          <circle cx="753" cy="366" r="17"/>
          <circle cx="663" cy="383" r="11"/>
          <circle cx="842" cy="383" r="11"/>
          <circle cx="674" cy="425" r="18"/>
          <circle cx="753" cy="430" r="20"/>
          <circle cx="833" cy="425" r="18"/>
        </g>
        <g class="bulb-icon" stroke="#fff" stroke-width="1.2" fill="none" stroke-linecap="round">
          <path d="M749 371 a6 6 0 1 1 8 0 v2 h-8z"/>
          <line x1="750" y1="376" x2="756" y2="376"/>
          <line x1="753" y1="353" x2="753" y2="356"/>
          <line x1="743" y1="357" x2="745" y2="359"/>
          <line x1="763" y1="357" x2="761" y2="359"/>
          <line x1="740" y1="365" x2="742" y2="365"/>
          <line x1="764" y1="365" x2="766" y2="365"/>
        </g>
        <g text-anchor="middle">
          <text x="663" y="386" font-size="7" style="fill:#fff">21%</text>
          <text x="842" y="386" font-size="7" style="fill:#fff">28%</text>
          <text x="674" y="429" font-size="9" style="fill:#fff">30%</text>
          <text x="753" y="434" font-size="9" style="fill:#fff">39%</text>
          <text x="833" y="429" font-size="9" style="fill:#fff">34%</text>
        </g>
      </g>
    </svg>
  </div>

  <div class="foot-band"></div>
</div>
</body>
</html>
```